Business Card for Professional Photographer

I'm looking for an eye catching modern clean design that compliments my logo/ website fonts & colours.
I specialise in architecture, corporate & commercial photography so I'm marketing to professional clients rather than portrait / wedding clients.

I would prefer to not have a solid black design.

My logo brand guide is as follows :

Main front font. : Reislust
Main font colour : #fff
Slogan front font : Ubuntu Bold
Monogram front font : Venti Medium
Container colour : #fff

I need print ready files in pdf .png & .eps formats.

Included in the files below are some screen grabs as reference to font & colours etc.

```html
<!DOCTYPE html>
<html lang="en">
<head>
<meta charset="utf-8">
<title>Clear Aperture — Business Card</title>
<link rel="stylesheet" href="https://fonts.googleapis.com/css2?family=Montserrat:wght@300;400;500;600&display=swap">
<style>
  :root {
    --canvas: #e9e8e6;
    --card-front: #77787a;
    --card-back: #ffffff;
    --gold: #c8954f;
    --gold-light: #e2c07a;
    --ink: #555659;
    --ink-soft: #8a8b8e;
    --white: #ffffff;
    --rule: #9a9b9e;
  }
  * { box-sizing: border-box; margin: 0; padding: 0; }
  html, body {
    width: 1200px; height: 874px; overflow: hidden;
    background: var(--canvas);
    font-family: "Montserrat", sans-serif;
  }
  .canvas {
    width: 1200px; height: 874px;
    display: flex; flex-direction: column; align-items: center; justify-content: center;
    gap: 40px;
  }
  .card {
    width: 620px; height: 354px; border-radius: 24px;
    position: relative; overflow: hidden;
    box-shadow: 0 6px 18px rgba(0,0,0,0.12);
  }
  /* Front */
  .card--front { background: var(--card-front); }
  .front-mark {
    position: absolute; left: 70px; top: 82px;
    width: 190px; height: 190px; border-radius: 50%;
    border: 9px solid var(--gold);
    background: transparent;
  }
  .front-brand {
    position: absolute; left: 320px; top: 142px;
    color: var(--white);
  }
  .brand-name {
    font-weight: 300; letter-spacing: 0.16em; text-transform: uppercase;
  }
  .front-brand .brand-name { font-size: 27px; }
  .brand-tagline {
    font-weight: 600; letter-spacing: 0.14em;
  }
  .front-brand .brand-tagline { font-size: 8.5px; margin-top: 4px; }
  .front-brand .brand-web { font-size: 13px; letter-spacing: 0.22em; margin-top: 6px; font-weight: 400; }

  /* Back */
  .card--back { background: var(--card-back); }
  .back-brand {
    position: absolute; left: 44px; top: 148px;
    display: flex; align-items: center; gap: 14px;
  }
  .back-mark {
    width: 46px; height: 46px; border-radius: 50%;
    border: 3px solid var(--gold);
  }
  .back-brand .brand-name { font-size: 19px; color: var(--ink); }
  .back-brand .brand-tagline { font-size: 6.5px; color: var(--ink-soft); margin-top: 3px; }
  .divider {
    position: absolute; left: 330px; top: 70px;
    width: 1.5px; height: 214px; background: var(--rule);
  }
  .contact {
    position: absolute; left: 356px; top: 66px;
    color: var(--ink);
  }
  .contact-name { font-size: 22px; font-weight: 500; color: var(--gold); letter-spacing: 0.02em; }
  .contact-title { font-size: 15px; margin-top: 1px; }
  .contact-address { font-size: 15px; line-height: 1.25; margin-top: 14px; }
  .contact-list { list-style: none; margin-top: 10px; font-size: 15px; line-height: 1.25; }
  .contact-list li { display: flex; align-items: center; gap: 8px; }
  .contact-list svg { width: 12px; height: 12px; fill: var(--gold); flex: none; }
</style>
</head>
<body>
<main class="canvas">
  <section class="card card--front" aria-label="Card front">
    <div class="front-mark" aria-hidden="true"></div>
    <div class="front-brand">
      <div class="brand-name">Clear Aperture</div>
      <div class="brand-tagline">Architecture Corporate Commercial</div>
      <div class="brand-web">www.clearaperture.com</div>
    </div>
  </section>

  <section class="card card--back" aria-label="Card back">
    <div class="back-brand">
      <div class="back-mark" aria-hidden="true"></div>
      <div>
        <div class="brand-name">Clear Aperture</div>
        <div class="brand-tagline">Architecture Corporate Commercial</div>
      </div>
    </div>
    <div class="divider"></div>
    <div class="contact">
      <div class="contact-name">Daniel Harper</div>
      <div class="contact-title">President</div>
      <div class="contact-address">4120 Birchwood Court<br>Juneau, Alaska 99801</div>
      <ul class="contact-list">
        <li><svg viewBox="0 0 12 12" aria-hidden="true"><path d="M2.5 0.5l2 2.2-1 1.3c.7 1.5 1.9 2.7 3.4 3.4l1.3-1 2.3 2-1 2.3C5 12.3-.3 7 .3 1.5z"/></svg>555-210-4418</li>
        <li><svg viewBox="0 0 12 12" aria-hidden="true"><path d="M3 0h6v12H3zM4 1v8.5h4V1zM5.5 10.2h1v1h-1z" fill-rule="evenodd"/></svg>555-374-9062</li>
        <li><svg viewBox="0 0 12 12" aria-hidden="true"><path d="M3 0h6v3H3zM0 4h12v5h-2v3H2V9H0zM3 8v3h6V8z" fill-rule="evenodd"/></svg>555-638-1275</li>
        <li><svg viewBox="0 0 12 12" aria-hidden="true"><path d="M0 2h12v8H0zM1 3l5 3.5L11 3z" fill-rule="evenodd"/></svg>hello@clearaperture.com</li>
        <li><svg viewBox="0 0 12 12" aria-hidden="true"><circle cx="6" cy="6" r="6"/></svg>www.clearaperture.com</li>
      </ul>
    </div>
  </section>
</main>
</body>
</html>
```